Request for Business Card Design

Hi. My name is Marlene, I am looking for a new business card design for my company, Quarrow Signal Instruments, LLC. I really like the design you did for Tarsel Venture and was hoping you could do something similar using our full logo and our mark. I am also open to any raised texture design using our mark. I have attached our full logo, which would need to be somewhere on the card, as well as the mark in both outline and full form, as well as our brand colors / guide. The card does not have to be white, as long as our logo and mark appear. I actually like darker colored business cards more, but am open to all options. If you are interested in working with me, please let me know. We would also take the business card design into letterhead design if you can do that.

```html
<!DOCTYPE html>
<html lang="en">
<head>
<meta charset="utf-8">
<title>Quarrow Signal Instruments — Business Card</title>
<link rel="stylesheet" href="https://fonts.googleapis.com/css2?family=Barlow:wght@300;400;600;700&display=swap">
<style>
  :root {
    --backdrop: #7f97bd;
    --card-dark: #414245;
    --card-dark-deep: #333437;
    --brand-blue: #2aa3c9;
    --brand-blue-deep: #1890bb;
    --accent-orange: #ef7a2e;
    --ink-light: #ffffff;
    --ink-muted: #d9dde2;
  }
  html, body {
    margin: 0;
    width: 1200px;
    height: 876px;
    overflow: hidden;
    background: var(--backdrop);
    font-family: "Barlow", "Arial Narrow", sans-serif;
  }
  .stage {
    position: relative;
    width: 1200px;
    height: 876px;
  }
  .card {
    position: absolute;
    top: 283px;
    width: 540px;
    height: 309px;
    border-radius: 3px;
    overflow: hidden;
    box-shadow: 0 14px 30px rgba(30, 40, 70, 0.35);
  }
  .card--front { left: 40px; }
  .card--back {
    left: 620px;
    background: linear-gradient(135deg, var(--card-dark) 0%, #4b4c50 45%, var(--card-dark-deep) 100%);
  }
  .card svg { position: absolute; inset: 0; }

  .contact {
    position: absolute;
    left: 28px;
    top: 26px;
    margin: 0;
    padding: 0;
    list-style: none;
    color: var(--ink-light);
    font-size: 12px;
    line-height: 15px;
    font-weight: 400;
  }
  .contact__row {
    display: flex;
    align-items: flex-start;
    gap: 10px;
    margin-bottom: 8px;
  }
  .contact__icon {
    flex: none;
    width: 22px;
    height: 22px;
    border-radius: 50%;
    background: var(--ink-light);
    display: flex;
    align-items: center;
    justify-content: center;
  }
  .contact__text { padding-top: 0; }

  .brand {
    position: absolute;
    display: flex;
    align-items: center;
    gap: 12px;
    color: var(--ink-light);
    font-weight: 700;
  }
  .brand__dot {
    flex: none;
    border-radius: 50%;
    border: 5px solid var(--ink-light);
    box-sizing: border-box;
  }
  .brand__name {
    display: flex;
    flex-direction: column;
    line-height: 1;
    letter-spacing: 0.06em;
  }
  .brand__sub { letter-spacing: 0.02em; margin-top: 3px; }

  .card--front .brand { right: 42px; top: 110px; }
  .card--front .brand__dot { width: 38px; height: 38px; }
  .card--front .brand__word { font-size: 38px; }
  .card--front .brand__sub { font-size: 10.5px; }

  .card--back .brand { left: 70px; top: 112px; }
  .card--back .brand__dot { width: 50px; height: 50px; border-width: 6px; }
  .card--back .brand__word { font-size: 46px; }
  .card--back .brand__sub { font-size: 12.5px; }

  .holder {
    position: absolute;
    right: 150px;
    bottom: 26px;
    color: var(--ink-light);
    text-align: right;
  }
  .holder__name {
    margin: 0;
    font-size: 22px;
    letter-spacing: 0.04em;
    text-transform: uppercase;
    line-height: 1.1;
  }
  .holder__first { font-weight: 700; }
  .holder__last { font-weight: 300; }
  .holder__role {
    margin: 2px 0 0;
    font-size: 15px;
    font-weight: 300;
    color: var(--ink-muted);
  }
</style>
</head>
<body>
<main class="stage">

  <section class="card card--front" aria-label="Business card front">
    <svg width="540" height="309" viewBox="0 0 540 309" aria-hidden="true">
      <defs>
        <linearGradient id="blueField" x1="0" y1="0" x2="1" y2="1">
          <stop offset="0" stop-color="#36aed2"/>
          <stop offset="1" stop-color="#1590bb"/>
        </linearGradient>
        <linearGradient id="darkField" x1="0" y1="0" x2="1" y2="1">
          <stop offset="0" stop-color="#4a4b4f"/>
          <stop offset="1" stop-color="#323336"/>
        </linearGradient>
      </defs>
      <rect width="540" height="309" fill="url(#blueField)"/>
      <path d="M0,150 C40,215 130,232 235,222 C340,212 420,250 470,309 L0,309 Z" fill="var(--accent-orange)"/>
      <path d="M0,170 C50,225 140,240 240,232 C345,224 425,260 470,309 L0,309 Z" fill="url(#darkField)"/>
    </svg>

    <ul class="contact">
      <li class="contact__row">
        <span class="contact__icon">
          <svg width="12" height="12" viewBox="0 0 12 12" aria-hidden="true"><rect x="3.5" y="1" width="5" height="10" rx="1" fill="none" stroke="#1f97c0" stroke-width="1.3"/><circle cx="6" cy="9.2" r="0.7" fill="#1f97c0"/></svg>
        </span>
        <span class="contact__text">+000 55510 2468<br>+000 55510 2468</span>
      </li>
      <li class="contact__row">
        <span class="contact__icon">
          <svg width="12" height="12" viewBox="0 0 12 12" aria-hidden="true"><rect x="1" y="4" width="5" height="4" rx="2" fill="none" stroke="#1f97c0" stroke-width="1.3"/><rect x="6" y="4" width="5" height="4" rx="2" fill="none" stroke="#1f97c0" stroke-width="1.3"/></svg>
        </span>
        <span class="contact__text">hello@quarrow.com<br>quarrowsignal.com</span>
      </li>
      <li class="contact__row">
        <span class="contact__icon">
          <svg width="12" height="12" viewBox="0 0 12 12" aria-hidden="true"><path d="M6 11 C3 7.5 2.5 6 2.5 4.6 A3.5 3.5 0 0 1 9.5 4.6 C9.5 6 9 7.5 6 11 Z" fill="#1f97c0"/><circle cx="6" cy="4.6" r="1.3" fill="#fff"/></svg>
        </span>
        <span class="contact__text">Street Address Here<br>Lakeport, 4410</span>
      </li>
    </ul>

    <div class="brand">
      <span class="brand__dot"></span>
      <span class="brand__name">
        <span class="brand__word">QUARROW</span>
        <span class="brand__sub">SIGNAL INSTRUMENTS</span>
      </span>
    </div>

    <div class="holder">
      <p class="holder__name"><span class="holder__first">Dorian</span><span class="holder__last">Vesk</span></p>
      <p class="holder__role">Director</p>
    </div>
  </section>

  <section class="card card--back" aria-label="Business card back">
    <div class="brand">
      <span class="brand__dot"></span>
      <span class="brand__name">
        <span class="brand__word">QUARROW</span>
        <span class="brand__sub">SIGNAL INSTRUMENTS</span>
      </span>
    </div>
  </section>

</main>
</body>
</html>
```